Marlow Vale Stud website

We would like to create a horse stud/agistment farm website similar to this websites we have attached below:
www.thornbeck.com.au
www.quillstead.com.au
www.brackley.com
www.pimsey.com.au
The main colour scheme are purple and white to align with the stable's racing colours.
We have also attach the company logo and also images of the farm and create some ideas for the website.
Many thanks for looking into this project!

```html
<!DOCTYPE html>
<html lang="en">
<head>
<meta charset="utf-8">
<title>Marlow Vale Stud</title>
<link href="https://fonts.googleapis.com/css2?family=Montserrat:wght@400;600;700;800&family=Open+Sans:wght@400;600;700&display=swap" rel="stylesheet">
<style>
:root{
  --purple:#3b1a3d;
  --purple-deep:#2d1030;
  --beige:#e5d9cc;
  --ghost:rgba(80,60,70,.16);
  --ink:#2a2226;
  --muted:#5d5157;
  --white:#ffffff;
  --band:#1f1a18;
}
*{box-sizing:border-box;margin:0;padding:0}
html,body{width:1200px;height:4986px;overflow:hidden}
body{font-family:"Open Sans",sans-serif;color:var(--ink);background:var(--beige)}
.page{position:relative;width:1200px;height:4986px;overflow:hidden;background:linear-gradient(180deg,#e6dbce,#ddd0c1 50%,#e4d8ca)}
.abs{position:absolute}
.ph{position:absolute;display:block}

/* header */
.topbar{left:0;top:0;width:1200px;height:66px;background:var(--white)}
.brand{left:120px;top:0;width:186px;height:126px;background:var(--purple);display:flex;align-items:center;justify-content:center;text-align:center;z-index:3}
.brand span{font-family:"Montserrat",sans-serif;font-weight:700;color:var(--white);font-size:18px;letter-spacing:2px;line-height:1.3}
.nav{left:558px;top:22px;display:flex;gap:12px;font-family:"Montserrat",sans-serif;font-size:14px;font-weight:600;color:var(--purple);z-index:3;white-space:nowrap}
.nav a{color:inherit;text-decoration:none;position:relative;padding:2px 6px;white-space:nowrap}
.nav a.current{border:2px solid var(--purple)}
.nav a.current::after{content:"";position:absolute;left:50%;bottom:-10px;margin-left:-6px;border:6px solid transparent;border-top-color:var(--purple)}

/* hero */
.hero{left:0;top:66px;width:1200px;height:650px;background:linear-gradient(100deg,#6e2a22 0%,#8a3d2c 35%,#a65a3f 60%,#c4a893 100%)}
.hero-arrow{top:330px;width:40px;height:56px}
.welcome{left:0;top:582px;width:492px;height:100px;background:rgba(40,22,30,.8);text-align:center;color:var(--white);padding-top:18px}
.welcome small{display:block;font-size:14px;letter-spacing:1px}
.welcome strong{display:block;font-family:"Montserrat",sans-serif;font-size:30px;font-weight:700;letter-spacing:1px;margin-top:8px}

/* section titles */
.ghost{font-family:"Montserrat",sans-serif;font-weight:800;color:var(--ghost);font-size:92px;letter-spacing:2px;white-space:nowrap}
.title{font-family:"Montserrat",sans-serif;font-weight:700;color:var(--purple);font-size:44px;width:1200px;left:0;text-align:center}

/* about */
.founded{left:190px;top:790px;font-family:"Montserrat",sans-serif;font-weight:700;font-size:18px;color:var(--purple)}
.year{left:180px;top:812px;font-family:"Montserrat",sans-serif;font-weight:800;font-size:140px;color:#6a5864;letter-spacing:-4px;line-height:1}
.about-card{left:592px;top:841px;width:538px;height:356px;background:var(--white);padding:22px 24px;box-shadow:0 6px 14px rgba(0,0,0,.15)}
.about-card h2{font-family:"Montserrat",sans-serif;font-weight:700;font-size:38px;color:var(--purple)}
.about-card p{font-size:18px;line-height:1.85;color:var(--muted);margin-top:6px}
.btn{display:flex;height:48px;margin-top:26px}
.btn b{background:var(--purple);color:var(--white);font-family:"Montserrat",sans-serif;font-size:13px;font-weight:600;letter-spacing:1px;width:126px;display:flex;align-items:center;justify-content:center}
.btn i{width:48px;border:2px solid var(--purple);border-left:0;display:flex;align-items:center;justify-content:center;background:var(--white)}

/* services */
.band{left:0;top:1549px;width:1200px;height:273px;background:var(--band)}
.service{top:1479px;width:296px;height:426px}
.service .label{position:absolute;left:50%;bottom:4px;transform:translateX(-50%);background:var(--purple);color:var(--white);font-family:"Montserrat",sans-serif;font-weight:700;font-size:21px;letter-spacing:2px;padding:8px 20px;white-space:nowrap}

/* blog */
.post{top:2985px;width:309px}
.post .img{position:relative;width:309px;height:233px}
.post h3{font-family:"Montserrat",sans-serif;font-weight:700;font-size:18px;color:var(--ink);line-height:1.4;margin-top:36px;height:54px}
.post .date{font-size:10px;color:var(--muted);margin-top:8px}
.post p{font-size:11px;line-height:1.45;color:var(--muted);margin-top:10px}
.post .more{display:inline-block;font-size:11px;font-weight:600;color:var(--ink);border-bottom:1px solid var(--ink);margin-top:18px}
.dots{left:580px;top:3454px;display:flex;gap:6px}
.dots span{width:10px;height:10px;border-radius:50%;border:1.5px solid var(--purple)}
.dots span.on{background:var(--purple)}

/* contact */
.field{background:var(--white);border-radius:36px;box-shadow:0 6px 12px rgba(0,0,0,.12);font-size:16px;color:var(--muted);padding:0 34px;display:flex;align-items:center}
.field.area{align-items:flex-start;padding-top:26px;border-radius:40px}
.submit{left:495px;top:4335px}
.submit .btn{margin:0;height:48px}

/* map & footer */
.map{left:0;top:4448px;width:1200px;height:438px;background:linear-gradient(135deg,#b3a3b1,#9d8b9b 60%,#a696a4)}
.footer{left:0;top:4886px;width:1200px;height:100px;background:var(--purple-deep);color:var(--white)}
.footer .name{left:130px;top:38px;font-family:"Montserrat",sans-serif;font-weight:700;font-size:19px;letter-spacing:1px}
.footer .copy{left:482px;top:42px;font-size:14px}
</style>
</head>
<body>
<div class="page">

  <div class="abs topbar"></div>
  <div class="abs brand"><span>MARLOW VALE<br>STUD.</span></div>
  <nav class="abs nav">
    <a class="current" href="#">HOME</a><a href="#">SERVICES</a><a href="#">ABOUT US</a><a href="#">TESTIMONIALS</a><a href="#">CONTACT</a><a href="#">FAQ</a>
  </nav>

  <div class="ph hero" role="img" aria-label="Horse leaning over a red stable door being fed by a young woman"></div>
  <svg class="abs hero-arrow" style="left:60px" viewBox="0 0 40 56"><path d="M28 4 8 28l20 24" fill="none" stroke="#fff" stroke-width="3"/></svg>
  <svg class="abs hero-arrow" style="left:1100px" viewBox="0 0 40 56"><path d="M12 4l20 24-20 24" fill="none" stroke="#fff" stroke-width="3"/></svg>
  <div class="abs welcome"><small>WELCOME TO</small><strong>MARLOW VALE STUD.</strong></div>

  <!-- about -->
  <div class="abs ghost" style="left:725px;top:752px">ABOUT US</div>
  <div class="abs founded">FOUNDED</div>
  <div class="abs year">2007</div>
  <div class="ph" role="img" aria-label="Bay horse cantering" style="left:133px;top:858px;width:415px;height:355px;background:radial-gradient(ellipse at 55% 50%,#5a2e1c 0%,#6f3a22 35%,rgba(111,58,34,0) 65%)"></div>
  <div class="abs about-card">
    <h2>ABOUT US</h2>
    <p>Lorem ipsum dolor sit amet, consectetur adipiscing elit, sed do eiusmod tempor incididunt ut labore et dolore magna aliqua. Quis ipsum suspendisse ultrices gravida. Risus commodo viverra maecenas accumsan lacus vel facilisis. Lorem ipsum dolor sit amet.</p>
    <div class="btn"><b>READ MORE</b><i><svg width="12" height="18" viewBox="0 0 12 18"><path d="M2 2l7 7-7 7" fill="none" stroke="#3b1a3d" stroke-width="2"/></svg></i></div>
  </div>
  <div class="ph" role="img" aria-label="Purple riding helmet and boot" style="left:1098px;top:1120px;width:102px;height:115px;background:radial-gradient(circle at 60% 40%,#4a2a5a,#3b1a3d 55%,rgba(59,26,61,0) 72%)"></div>

  <!-- services -->
  <div class="abs ghost" style="left:0;width:1200px;text-align:center;top:1320px;font-size:80px">SERVICES</div>
  <h2 class="abs title" style="top:1343px">SERVICES</h2>
  <div class="abs band"></div>
  <div class="abs service" style="left:100px">
    <div class="ph" role="img" aria-label="Two horses looking over a stable fence" style="inset:0;background:linear-gradient(180deg,#5f7a3e,#6e4a2f 45%,#5a3a28)"></div>
    <div class="label">FACILITY HIRE</div>
  </div>
  <div class="abs service" style="left:452px">
    <div class="ph" role="img" aria-label="Two horses eating hay together" style="inset:0;background:linear-gradient(180deg,#6f8d4a,#2e2420 45%,#b99a55)"></div>
    <div class="label">AGISTMENT</div>
  </div>
  <div class="abs service" style="left:801px">
    <div class="ph" role="img" aria-label="Chestnut horse head with white blaze" style="inset:0;background:linear-gradient(180deg,#8a6a3c,#a4562c 50%,#7d4b2b)"></div>
    <div class="label">AMBER CREST</div>
  </div>

  <!-- gallery -->
  <div class="abs ghost" style="left:0;width:1200px;text-align:center;top:2000px;font-size:80px">PHOTOS</div>
  <h2 class="abs title" style="top:2024px">GALLERY</h2>
  <div class="ph" role="img" aria-label="Palomino horse in a green paddock" style="left:150px;top:2144px;width:495px;height:539px;background:linear-gradient(180deg,#3f5b2e,#c9b58f 45%,#5f8a3c);box-shadow:0 6px 12px rgba(0,0,0,.2)"></div>
  <div class="ph" role="img" aria-label="Chestnut horse grazing from a tyre feeder" style="left:675px;top:2151px;width:439px;height:239px;background:linear-gradient(160deg,#5f8a3e,#7a4a2a 45%,#6a9444);border:3px solid #2a1f20"></div>
  <div class="ph" role="img" aria-label="Dark mare with foal in a field" style="left:675px;top:2443px;width:439px;height:240px;background:linear-gradient(180deg,#58763c,#3a2621 50%,#6c9248);border:3px solid #2a1f20"></div>
  <div class="ph" role="img" aria-label="Saddle on a stand with hay bale" style="left:0;top:2593px;width:332px;height:266px;background:radial-gradient(ellipse at 40% 70%,#c79b4e 0%,#b6883e 40%,rgba(182,136,62,0) 70%)"></div>

  <!-- blog -->
  <div class="abs ghost" style="left:0;width:1200px;text-align:center;top:2866px;font-size:80px">BLOG</div>
  <h2 class="abs title" style="top:2890px">OUR BLOG</h2>
  <article class="abs post" style="left:120px">
    <div class="img" role="img" aria-label="Two bay horses nuzzling" style="background:linear-gradient(150deg,#3c5a2a,#7a3e22 50%,#5a3a24)"></div>
    <h3>CONSTRUCTION FORKLIFT BUYERS GUIDE</h3>
    <div class="date">&#9635; 12 DECEMBER 2016</div>
    <p>Lorem ipsum dolor sit amet, sed diam nonumy eirmod tempor invidunt ut labore et dolore magna aliquyam erat sed voluptua at vero.</p>
    <span class="more">READ MORE</span>
  </article>
  <article class="abs post" style="left:452px">
    <div class="img" role="img" aria-label="Woman stroking a dark horse" style="background:linear-gradient(150deg,#4a5a3a,#3a2a28 50%,#8a6048)"></div>
    <h3>HOW TO PLAN FOR YOUR DREAM HOUSE?</h3>
    <div class="date">&#9635; 12 DECEMBER 2016</div>
    <p>Lorem ipsum dolor sit amet, sed diam nonumy eirmod tempor invidunt ut labore et dolore magna aliquyam erat sed voluptua at vero.</p>
    <span class="more">READ MORE</span>
  </article>
  <article class="abs post" style="left:788px">
    <div class="img" role="img" aria-label="Man standing beside a horse outdoors" style="background:linear-gradient(150deg,#4e6a34,#8a6a48 50%,#c29a5e)"></div>
    <h3>BUILDER OF HUMAN HAPPINESS FOR ALL TIME</h3>
    <div class="date">&#9635; 12 DECEMBER 2016</div>
    <p>Lorem ipsum dolor sit amet, sed diam nonumy eirmod tempor invidunt ut labore et dolore magna aliquyam erat sed voluptua at vero.</p>
    <span class="more">READ MORE</span>
  </article>
  <div class="abs dots"><span class="on"></span><span></span><span></span></div>

  <!-- contact -->
  <div class="abs ghost" style="left:0;width:1200px;text-align:center;top:3558px;font-size:80px">CONTACT</div>
  <h2 class="abs title" style="top:3582px">CONTACT US</h2>
  <div class="abs field" style="left:126px;top:3680px;width:948px;height:73px">YOUR NAME</div>
  <div class="abs field" style="left:126px;top:3806px;width:456px;height:72px">YOUR MAIL</div>
  <div class="abs field" style="left:618px;top:3806px;width:456px;height:72px">YOUR PHONE</div>
  <div class="abs field area" style="left:126px;top:3929px;width:948px;height:312px">YOUR MESSAGE</div>
  <div class="abs submit"><div class="btn"><b style="width:138px;font-size:15px;letter-spacing:3px">SUBMIT</b><i><svg width="12" height="18" viewBox="0 0 12 18"><path d="M2 2l7 7-7 7" fill="none" stroke="#3b1a3d" stroke-width="2"/></svg></i></div></div>

  <!-- map -->
  <div class="ph map" role="img" aria-label="Street map showing the stud location"></div>
  <svg class="abs" style="left:598px;top:4620px" width="30" height="44" viewBox="0 0 30 44"><path d="M15 1C7 1 1 7 1 15c0 11 14 28 14 28s14-17 14-28C29 7 23 1 15 1z" fill="#2d1030"/><circle cx="15" cy="15" r="5" fill="#a897a6"/></svg>

  <footer class="abs footer">
    <div class="abs name">MARLOW VALE STUD.</div>
    <div class="abs copy">Copyrights 2016. All rights reserved</div>
  </footer>
</div>
</body>
</html>
```